Website Development for vaultmerrow.com.au

Build a new Wordpress/Responsive website for vaultmerrow.com.au

Target Market(s)

Compliance Managers, Risk Managers, Information Security and Cyber Security Professionals, Chief Data/Digital Officers, Chief Operating/Financial Officers, Business Continuity Professionals, Disaster Recovery Planners, Small Business Owners, Local/Federal Government entities

Industry/Entity Type

Data Service

Coding

Coded - Design and coding required

Number of Pages Required

5+ page

Font styles to use
Sans Serif

Colors

Designer to choose colors to be used in the design.

Requirements
Must have
• 1. Site Structure: Home Page plus the following chapter-pages for a) Services b) About c) Resources d) Blog e) Contact Us
• 2. Prefer site to built on wordpress and we can purchase a theme if needed (we currently use Kelp9 for other sites)
• 3. Blog needs to be wordpress based
• 4. We will host the site ourselves on our own servers
• 5. Responsive Design
Nice to have
• 1. Livechat capability/interface
• 2. Capability for marketing automation integration (such as hubspot, marketo, infusionsoft etc)
• 3. Capability for CRM integration (Salesforce)

```html
<!DOCTYPE html>
<html lang="en">
<head>
<meta charset="utf-8">
<title>Contact Us – Vaultmerrow</title>
<link href="https://fonts.googleapis.com/css2?family=Roboto:wght@400;500;700&family=Mulish:wght@400;600;700&display=swap" rel="stylesheet">
<style>
:root{
  --red:#e31e26;
  --red-deep:#8e0f16;
  --ink:#2b2b2b;
  --muted:#555;
  --gray-bar:#8c8c8f;
  --footer:#7b7b7e;
  --pale:#f2f2f2;
  --white:#fff;
}
*{margin:0;padding:0;box-sizing:border-box}
html,body{width:762px;height:1200px;overflow:hidden}
body{font-family:"Mulish",sans-serif;color:var(--ink);background:var(--white);position:relative}
.abs{position:absolute}
.brand{font-family:"Roboto",sans-serif;font-weight:500;color:var(--red);display:flex;align-items:center;gap:6px}
.brand .dot{width:14px;height:14px;border-radius:50%;background:currentColor}
.topbar{left:0;top:0;width:762px;height:30px;background:var(--gray-bar);color:var(--white);font-size:9px;display:flex;align-items:center;padding:0 90px;gap:20px}
.topbar .item{display:flex;align-items:center;gap:6px}
.topbar .follow{margin-left:auto;font-weight:700;display:flex;align-items:center;gap:5px}
.topbar .sq{width:14px;height:14px;display:inline-block}
.nav{left:0;top:30px;width:762px;height:52px;background:var(--white);display:flex;align-items:center;padding:0 92px 0 90px}
.nav .brand{font-size:24px}
.nav ul{margin-left:auto;display:flex;gap:22px;list-style:none;font-family:"Roboto",sans-serif;font-size:9px;height:52px;align-items:center}
.nav li{height:52px;display:flex;align-items:center}
.nav li.active{color:var(--red);border-bottom:3px solid var(--red)}
.hero{left:0;top:82px;width:762px;height:250px;background:var(--pale);overflow:hidden}
.hero-photo{left:0;top:0;width:762px;height:230px;background:radial-gradient(circle at 72% 38%,#e2323a 0,#b3141c 30%,#5a0b10 75%,#3a070a 100%)}
.hero h1{left:90px;top:38px;color:var(--white);font-family:"Roboto",sans-serif;font-weight:400;font-size:26px;line-height:34px;letter-spacing:.5px}
.hero h1 b{font-weight:700}
.hero h1 span{display:block;font-size:17px;line-height:30px}
.crumb{left:90px;top:312px;font-family:"Roboto",sans-serif;font-size:9px;color:var(--ink)}
.crumb em{font-style:normal;color:var(--red);font-weight:500;margin-left:6px}
.section-title{left:0;width:762px;text-align:center;font-family:"Roboto",sans-serif;font-weight:500}
.contact-title{top:374px;font-size:27px;color:var(--ink)}
.intro{left:160px;top:420px;width:442px;text-align:center;font-size:7.5px;line-height:12px;color:var(--muted)}
.info-brand{left:157px;top:470px;font-size:28px}
.info{left:156px;width:170px;display:flex;gap:10px}
.info .ic{width:27px;height:27px;border-radius:50%;background:#8c8c8f;flex:none;display:flex;align-items:center;justify-content:center}
.info h4{font-family:"Roboto",sans-serif;font-weight:400;font-size:10px;margin-top:1px}
.info p{font-size:8.5px;line-height:12px;color:var(--muted);margin-top:2px}
.map{left:350px;top:462px;width:274px;height:284px;background:var(--white);box-shadow:0 0 6px rgba(0,0,0,.15);padding:5px}
.map div{width:100%;height:100%;background:linear-gradient(160deg,#eceee8,#e3e6de 60%,#eef0ea)}
.started{left:0;top:790px;width:762px;height:298px;background:linear-gradient(180deg,#e7373d,#e2262d 60%,#d91f26)}
.started-title{top:854px;font-size:25px;color:var(--white)}
.form{left:198px;top:910px;width:409px;height:89px;border:1px solid rgba(255,255,255,.55);display:grid;grid-template-columns:205px 1fr;color:rgba(255,255,255,.9);font-size:8px}
.form .col{border-right:1px solid rgba(255,255,255,.55);display:flex;flex-direction:column}
.form .field{flex:1;padding:10px 11px 0;border-bottom:1px solid rgba(255,255,255,.55)}
.form .field:first-child{border-bottom-color:var(--white)}
.form .field:last-child{border-bottom:none}
.form .msg{padding:10px 13px}
.submit{left:340px;top:1021px;width:82px;height:22px;background:#111;border-radius:11px;color:var(--white);font-family:"Roboto",sans-serif;font-weight:500;font-size:9px;display:flex;align-items:center;padding-left:30px}
.submit .dot{position:absolute;left:4px;top:3px;width:16px;height:16px;border-radius:50%;background:var(--red)}
.chat{left:647px;top:1073px;width:27px;height:27px;border-radius:50%;background:var(--white);box-shadow:0 2px 5px rgba(0,0,0,.3);display:flex;align-items:center;justify-content:center}
.footer{left:0;top:1088px;width:762px;height:112px;background:var(--footer);color:var(--white)}
.footer .brand{position:absolute;left:90px;top:26px;color:var(--white);font-size:28px}
.footer ul{position:absolute;right:92px;top:48px;display:flex;gap:25px;list-style:none;font-family:"Roboto",sans-serif;font-size:8.5px}
.footer .rule{position:absolute;left:90px;right:92px;top:85px;border-top:1px solid rgba(255,255,255,.25)}
.footer .copy{position:absolute;left:90px;right:92px;top:93px;display:flex;justify-content:space-between;font-size:7.5px}
</style>
</head>
<body>

<header class="topbar abs">
  <span class="item">
    <svg width="12" height="12" viewBox="0 0 24 24" fill="none" stroke="#fff" stroke-width="2"><path d="M5 3h4l2 5-3 2a12 12 0 0 0 6 6l2-3 5 2v4a2 2 0 0 1-2 2A17 17 0 0 1 3 5a2 2 0 0 1 2-2z"/></svg>
    +012-555-019
  </span>
  <span class="item">
    <svg width="12" height="10" viewBox="0 0 24 18" fill="none" stroke="#fff" stroke-width="2"><rect x="1" y="1" width="22" height="16"/><path d="M1 1l11 9 11-9"/></svg>
    info@vaultmerrow.com.au
  </span>
  <span class="follow">Follow Us on
    <i class="sq" style="background:#e94b35"></i><i class="sq" style="background:#1da1f2"></i><i class="sq" style="background:#0a66c2"></i><i class="sq" style="background:#e62117"></i>
  </span>
</header>

<nav class="nav abs">
  <div class="brand"><span class="dot"></span>Vaultmerrow</div>
  <ul>
    <li>HOME</li><li>ABOUT</li><li>SERVICES</li><li>RESOURCES</li><li>BLOG</li><li class="active">CONTACT US</li>
  </ul>
</nav>

<section class="hero abs">
  <div class="hero-photo abs" role="img" aria-label="Hands holding a glowing red sphere of data service icons over a dark red backdrop"></div>
  <svg class="abs" style="left:0;top:150px" width="762" height="100" viewBox="0 0 762 100" preserveAspectRatio="none"><path d="M0 40 C200 110 520 110 762 20 V100 H0Z" fill="#f2f2f2"/></svg>
  <h1 class="abs">DELIVERING <b>QUALITY</b><br>SERVICES THROUGH<br><b>INNOVATION</b><span>From Industry&nbsp; Experts</span></h1>
</section>
<div class="crumb abs">HOME &nbsp;»<em>CONTACT US</em></div>

<h2 class="section-title contact-title abs">CONTACT US</h2>
<p class="intro abs">The point of using Lorem Ipsum is that it has a more-or-less normal distribution of letters, as opposed to using ‘Content here, content here’, making it look like readable English</p>

<div class="brand info-brand abs"><span class="dot" style="width:20px;height:20px"></span>Vaultmerrow</div>

<div class="info abs" style="top:538px">
  <span class="ic"><svg width="12" height="14" viewBox="0 0 24 28" fill="none" stroke="#fff" stroke-width="2.2"><path d="M12 26s9-9 9-15a9 9 0 0 0-18 0c0 6 9 15 9 15z"/><circle cx="12" cy="11" r="3"/></svg></span>
  <div><h4>ADDRESS</h4><p>123, Lorem ipsum dolor sit amet, consectetur adipiscing elit</p></div>
</div>
<div class="info abs" style="top:594px">
  <span class="ic"><svg width="12" height="10" viewBox="0 0 24 18" fill="none" stroke="#fff" stroke-width="2.2"><rect x="1" y="1" width="22" height="16" rx="2"/><path d="M1 2l11 8 11-8"/></svg></span>
  <div><h4>MAIL US ON:</h4><p>info@vaultmerrow.com.au</p></div>
</div>
<div class="info abs" style="top:641px">
  <span class="ic"><svg width="12" height="12" viewBox="0 0 24 24" fill="none" stroke="#fff" stroke-width="2.2"><path d="M5 3h4l2 5-3 2a12 12 0 0 0 6 6l2-3 5 2v4a2 2 0 0 1-2 2A17 17 0 0 1 3 5a2 2 0 0 1 2-2z"/></svg></span>
  <div><h4>CALL US ON:</h4><p>+1 555-014-2290</p></div>
</div>
<div class="info abs" style="top:688px">
  <span class="ic"><svg width="12" height="12" viewBox="0 0 24 24" fill="none" stroke="#fff" stroke-width="2.2"><rect x="3" y="8" width="18" height="13" rx="2"/><path d="M7 8V3h10v5M7 13h10M7 17h6"/></svg></span>
  <div><h4>FOR FAX:</h4><p>+1 555-014-2290</p></div>
</div>

<div class="map abs"><div role="img" aria-label="Road map of the central United States around Colorado, Nebraska and Kansas"></div></div>

<section class="started abs" role="img" aria-label="Business team meeting around a table, tinted red"></section>
<h2 class="section-title started-title abs">LET’S GET STARTED</h2>
<form class="form abs">
  <div class="col">
    <div class="field">Your Name*</div>
    <div class="field">Your Email*</div>
    <div class="field">Your Contact Number*</div>
  </div>
  <div class="msg">Your Message*</div>
</form>
<div class="submit abs"><span class="dot"></span>Submit</div>

<footer class="footer abs">
  <div class="brand"><span class="dot" style="width:20px;height:20px"></span>Vaultmerrow</div>
  <ul><li>HOME</li><li>ABOUT</li><li>SERVICES</li><li>RESOURCES</li><li>BLOG</li><li>CONTACT US</li></ul>
  <div class="rule"></div>
  <div class="copy"><span>Copyright 2019 @ Vaultmerrow. All Rights Reserved.</span><span>Terms of Services / Privacy Policy</span></div>
</footer>

<div class="chat abs"><svg width="14" height="12" viewBox="0 0 24 20"><path d="M2 2h20v12H9l-5 4v-4H2z" fill="#e31e26"/><circle cx="8" cy="8" r="1.4" fill="#fff"/><circle cx="12" cy="8" r="1.4" fill="#fff"/><circle cx="16" cy="8" r="1.4" fill="#fff"/></svg></div>

</body>
</html>
```